Sustainably Transforming Education

Company is education services based. early learning through adult and corporate. Focus is national government policy and program design and delivery alongside a research based and academically grounded set of approaches to planning, evaluation, and change management.I am looking for an innovative design position that aligns with the global agendas for innovation, creativity and collaboration at international and national policy levels (berulo is a name that reflects these qualities - colours need to reflect amythyst in some way). I also need a design that translates from a business card as 1 medium of interaction to a template that can work in word/powerpoint etc to support both stationery as well as a digital strategy across multiple channels (fb/twit/etc)There is no slogan/tag line for the company and their is no logo. I was looking to just leverage the name - have currently played around with various fonts (ending up with cuisine - all lowercase).

Industry/Entity Type

Adult

Contact Information for Business Card

name: berulo (all lowercase)Chairman: Andrew CrowMobile: +61 418 902 131Web: www.berulo.comemail: martin.pelly@berulo-example.com

Font styles to use
Script
Other font styles liked:
• cuisine

Colors
e34298
e667a6
33a6d7
aaaaaa

Requirements
Nice to have
• https://files.example-share.net/sh/qx7kw2hd91lzmnp/AAFr3tYbQeLp8VwZnKcDs2Hu?dl=0
• Link to the printwell templates used to begin this process....the one with the lines was about people intersecting (collaborating).....the organic shapes one more of a fluid feel of people coming together - the overall shape being largely spherical could represent a "global" feel.....anyway that is how I was thinking about these

```html
<!DOCTYPE html>
<html lang="en">
<head>
<meta charset="utf-8">
<title>berulo – business card, front and back</title>
<link rel="stylesheet" href="https://fonts.googleapis.com/css2?family=Kalam:wght@400;700&display=swap">
<style>
  :root {
    --page-bg: #ececec;
    --brand-blue: #33a6d7;
    --amethyst: #e34298;
    --amethyst-soft: #e667a6;
    --ink-black: #16181b;
    --charcoal: #282c30;
    --map-faint: #f1eef3;
    --map-dark: #30353a;
    --swoosh-grey: #aaaaaa;
    --paper: #ffffff;
    --script: "Kalam", cursive;
  }
  * { margin: 0; padding: 0; box-sizing: border-box; }
  html, body {
    width: 1200px;
    height: 1152px;
    overflow: hidden;
    background: var(--page-bg);
  }
  .sheet {
    width: 1200px;
    height: 1152px;
    display: flex;
    flex-direction: column;
    align-items: center;
    justify-content: center;
    gap: 64px;
  }
  .card {
    display: block;
    width: 840px;
    height: 480px;
    box-shadow: 0 6px 18px rgba(0, 0, 0, 0.18);
  }
  .fill-paper { fill: var(--paper); }
  .fill-blue { fill: var(--brand-blue); }
  .fill-amethyst { fill: var(--amethyst); }
  .fill-amethyst-soft { fill: var(--amethyst-soft); }
  .fill-charcoal { fill: var(--charcoal); }
  .fill-grey { fill: var(--swoosh-grey); }
  .map-area-light { fill: var(--map-faint); }
  .map-area-dark { fill: var(--map-dark); }
  .rule { stroke: var(--amethyst); stroke-width: 2; }
  .person-name { font-family: var(--script); font-weight: 700; font-size: 48px; fill: var(--brand-blue); }
  .person-role { font-family: var(--script); font-weight: 700; font-size: 30px; fill: var(--ink-black); }
  .contact-line { font-family: var(--script); font-weight: 400; font-size: 18px; fill: var(--ink-black); }
  .contact-icon { fill: var(--amethyst); }
  .wordmark-small { font-family: var(--script); font-weight: 700; font-size: 52px; fill: var(--paper); }
  .wordmark-large { font-family: var(--script); font-weight: 700; font-size: 104px; fill: var(--brand-blue); }
</style>
</head>
<body>
<main class="sheet">

  <!-- Front of card -->
  <svg class="card card-front" viewBox="0 0 840 480" xmlns="http://www.w3.org/2000/svg">
    <rect class="fill-paper" width="840" height="480"/>
    <path class="map-area-light" role="img" aria-label="Faint world map in the background"
          d="M380,110 C470,80 640,90 760,130 C800,170 790,240 740,280 C640,320 500,320 420,290 C360,250 340,160 380,110 Z"/>

    <!-- top bands -->
    <path class="fill-blue" d="M0,0 H840 V175 C640,70 380,55 150,118 C90,134 40,146 0,152 Z"/>
    <path class="fill-amethyst" d="M70,0 H840 V140 C640,45 390,30 170,82 C130,90 100,96 70,100 Z"/>

    <!-- bottom bands -->
    <path class="fill-amethyst" d="M0,250 C230,318 560,322 840,215 V245 C560,350 240,352 0,300 Z"/>
    <path class="fill-blue" d="M0,318 C250,362 580,360 840,262 V480 H0 Z"/>

    <!-- identity -->
    <text class="person-name" x="80" y="212">Martin Pelly</text>
    <text class="person-role" x="96" y="258">Chairman</text>
    <line class="rule" x1="80" y1="274" x2="430" y2="274"/>
    <line class="rule" x1="452" y1="110" x2="452" y2="250"/>

    <!-- contacts -->
    <g class="contact">
      <rect class="contact-icon" x="472" y="128" width="14" height="13" rx="3"/>
      <text class="contact-line" x="496" y="141">+61 427 315 086</text>
    </g>
    <g class="contact">
      <rect class="contact-icon" x="472" y="165" width="14" height="11" rx="2"/>
      <text class="contact-line" x="496" y="177">martin.pelly@berulo-example.com</text>
    </g>
    <g class="contact">
      <circle class="contact-icon" cx="479" cy="207" r="7"/>
      <text class="contact-line" x="496" y="213">www.berulo-example.com</text>
    </g>

    <text class="wordmark-small" x="70" y="430">berulo</text>
  </svg>

  <!-- Back of card -->
  <svg class="card card-back" viewBox="0 0 840 480" xmlns="http://www.w3.org/2000/svg">
    <rect class="fill-charcoal" width="840" height="480"/>
    <path class="map-area-dark" role="img" aria-label="Faint world map in the background"
          d="M170,120 C300,60 560,60 700,110 C760,160 740,240 660,270 C520,300 320,300 210,270 C140,230 120,160 170,120 Z"/>

    <path class="fill-grey" d="M0,262 C260,300 580,300 840,190 V250 C580,370 270,372 0,322 Z"/>
    <path class="fill-amethyst" d="M0,300 C270,348 580,346 840,238 V256 C580,372 270,374 0,330 Z"/>
    <path class="fill-blue" d="M0,330 C270,374 580,372 840,256 V480 H0 Z"/>

    <text class="wordmark-large" x="430" y="250" text-anchor="middle">berulo</text>
  </svg>

</main>
</body>
</html>
```